Orvane Thinner Logo and Packaging Design

We are seeking a striking and professional logo and packaging design for our new product line, Orvane Thinner. This logo will be used on the packaging for three different sizes of half-transparent carboys: 1L, 4L, and 20L. Orvane Thinner is a high-quality solvent brand known for its excellent solvency, fast-drying properties, and pleasant smell. The logo should feature an eagle motif to symbolize power and precision, and our slogan, "SOAR WITH CARE." The design should be suitable for placement on hardware store and warehouse shelves. Additionally, we need the designer to create an eagle logo to accompany the packaging.

Packaging Dimensions:
1L Carboy:
Front: 71mm height x 142mm width
Side: 71mm height x 73mm width
4L Carboy:
Front: 160mm height x 170mm width
Side: 160mm height x 120mm width
20L Carboy:
Front: 245mm height x 190mm width
Side: 215mm height x 190mm width
Front Label Requirements:

Product Name: Thinner QXR
Volume: 20L
Precautionary Statements:
Keep Away from Sources of ignition - No Smoking
Avoid Contact with Eyes
Do Not Empty into Drains or Sewers
Take Precautionary Measures Against Static Discharge
Hazard Statements:
Flammable Liquid and Vapor
May be fatal if swallowed or enters Airways
Causes Skin Irritation
Causes Serious Eye Irritation
Causes Damage to Organs if Prolonged or Repeated Exposure
Hazard Pictograms: (Include relevant hazard symbols)
Design Requirements:

Logo: Eagle motif (to be designed by the designer)
Slogan: SOAR WITH CARE
Color Scheme: Designer to recommend (should be striking and professional for retail display)

Please see my latest picture. Kindly note the packaging is in Plastic Carboy (not in metal tin as per PS).

Eagle to be more majestic and bigger (as if soaring in the sky).
Singapore landscape as background to have Singapore identity such as KTR, Corvale wheel, terrace at the cove etc.

Eagle to be more majestic and bigger, wings to spread wide.
We not want it to be of photo style, but more on a cartoon style. Please see my latest file uploaded.

Target Market(s)

Our target market includes painting companies, construction companies, direct household consumers, and industrial users who require high-quality solvents for various applications.

Industry/Entity Type

Chemical, spray paint and painting, household, industrial

Requirements
Must have
• Professional and Striking Design: Eye-catching and professional packaging for retail shelves. Eagle Logo: A strong, precise eagle logo. Slogan: "SOAR WITH CARE" prominently displayed. Clear Precautionary and Hazard Statements: Important safety information and pictograms. Volume Indication: Clearly marked (e.g., 1L, 4L, 20L). Eagle to be more majestic and bigger (as if soaring in the sky). Singapore landscape as background to have Singapore identity such as KTR, Corvale wheel, terrace at the cove etc.
Nice to have
• Color Scheme Recommendations: Suggestions for a professional, striking color scheme. Versatility: Design elements adaptable across different sizes of packaging. Environmentally Friendly Elements: Indications of sustainability or eco-friendliness in the design.
Should not have
• Overly Complex Designs: Avoid cluttered or overly intricate designs that detract from readability. Inconsistent Branding: Ensure all elements are cohesive and align with the brand identity.

```html
<!DOCTYPE html>
<html lang="en">
<head>
<meta charset="utf-8">
<title>Orvane Thinner – 20L Label</title>
<link href="https://fonts.googleapis.com/css2?family=Montserrat:wght@600;700;800;900&family=Roboto:wght@400;700&display=swap" rel="stylesheet">
<style>
  :root {
    --bg: #e8e8e8;
    --label: #f1f1f1;
    --orange: #e2603a;
    --ink: #2d2d2d;
    --white: #ffffff;
    --warn: #e8b21c;
  }
  * { box-sizing: border-box; margin: 0; padding: 0; }
  html, body { width: 1200px; height: 721px; overflow: hidden; background: var(--bg); }
  .canvas { position: relative; width: 1200px; height: 721px; }

  .panel { position: absolute; top: 90px; height: 540px; background: var(--label); overflow: hidden; }
  .panel--side { left: 170px; width: 300px; }
  .panel--front { left: 470px; width: 560px; border-left: 1px solid #dcdcdc; }

  .title { position: absolute; top: 30px; left: 0; right: 0; text-align: center;
    font-family: "Montserrat", sans-serif; font-weight: 900; color: var(--ink);
    line-height: .9; text-transform: uppercase; }
  .panel--side .title { font-size: 30px; }
  .panel--front .title { font-size: 54px; top: 14px; }
  .rule { position: absolute; height: 10px; background: var(--orange); }

  .side-block { position: absolute; left: 0; top: 130px; width: 270px; height: 150px;
    background: var(--orange); border-radius: 0 60px 60px 0; }

  .brand { position: absolute; left: 0; right: 0; text-align: center;
    font-family: "Montserrat", sans-serif; font-weight: 700; color: var(--ink);
    letter-spacing: .08em; text-transform: uppercase; white-space: nowrap; }
  .brand-dot { position: absolute; left: 50%; border-radius: 50%; background: var(--orange); }

  .tagline { position: absolute; left: 50%; transform: translateX(-50%);
    background: var(--orange); color: var(--white); border-radius: 0 0 30px 30px;
    font-family: "Montserrat", sans-serif; font-weight: 800; letter-spacing: .1em;
    text-align: center; white-space: nowrap; }

  .band { position: absolute; left: 0; right: 0; bottom: 0; height: 100px; background: var(--orange); }
  .volume { position: absolute; font-family: "Montserrat", sans-serif; font-weight: 800;
    color: var(--white); font-size: 56px; line-height: 1; }

  .safety { position: absolute; font-family: "Roboto", sans-serif; color: var(--ink);
    font-size: 9px; line-height: 1.4; white-space: nowrap; }
  .safety h3 { font-size: 10.5px; font-weight: 700; margin-bottom: 3px; }
  .safety ul { list-style: none; }
  .safety li::before { content: "• "; }

  .pictograms { position: absolute; left: 30px; bottom: 26px; display: flex; gap: 12px; }
</style>
</head>
<body>
<main class="canvas">

  <section class="panel panel--side" aria-label="Side label">
    <div class="rule" style="left:0;top:40px;width:18px"></div>
    <h2 class="title">Thinner<br>QXR</h2>
    <div class="side-block"></div>
    <span class="brand-dot" style="top:312px;width:36px;height:36px;margin-left:-18px"></span>
    <p class="brand" style="top:362px;font-size:17px">Orvane Thinner</p>
    <p class="tagline" style="top:392px;width:220px;padding:6px 0;font-size:11px">SOAR WITH CARE</p>
    <div class="band"><span class="volume" style="left:50%;transform:translateX(-50%);top:22px">20L</span></div>
  </section>

  <section class="panel panel--front" aria-label="Front label">
    <div class="rule" style="left:0;top:38px;width:62px"></div>
    <div class="rule" style="right:0;top:24px;width:62px"></div>
    <h1 class="title">Thinner<br>QXR</h1>
    <span class="brand-dot" style="top:130px;width:60px;height:60px;margin-left:-30px"></span>
    <p class="brand" style="top:204px;font-size:32px">Orvane Thinner</p>
    <p class="tagline" style="top:250px;width:340px;padding:10px 0;font-size:17px">SOAR WITH CARE</p>

    <div class="safety" style="left:24px;top:334px">
      <h3>Precautionary</h3>
      <ul>
        <li>Keep Away from Sources of ignition - No Smoking</li>
        <li>Avoid Contact with Eyes</li>
        <li>Do Not Empty into Drains or Sewers</li>
        <li>Take Precautionary Measures Against Static Discharge</li>
      </ul>
    </div>
    <div class="safety" style="left:290px;top:320px">
      <h3>Hazard</h3>
      <ul>
        <li>Flammable Liquid and Vapor</li>
        <li>May be fatal if swallowed or enters Airways</li>
        <li>Causes Skin Irritation</li>
        <li>Causes Serious Eye Irritation</li>
        <li>Causes Damage to Organs if Prolonged or Repeated Exposure</li>
      </ul>
    </div>

    <div class="band">
      <div class="pictograms" aria-label="Hazard pictograms">
        <svg width="48" height="42" viewBox="0 0 48 42" aria-label="Flammable"><polygon points="24,2 46,40 2,40" fill="var(--warn)" stroke="#222" stroke-width="2"/><path d="M24 16c5 6 7 10 4 16h-8c-3-5 0-9 4-16z" fill="#222"/></svg>
        <svg width="48" height="42" viewBox="0 0 48 42" aria-label="Toxic"><polygon points="24,2 46,40 2,40" fill="var(--warn)" stroke="#222" stroke-width="2"/><circle cx="24" cy="22" r="6" fill="#222"/><path d="M15 27l18 8M33 27l-18 8" stroke="#222" stroke-width="2.5"/></svg>
        <svg width="48" height="42" viewBox="0 0 48 42" aria-label="Health hazard"><polygon points="24,2 46,40 2,40" fill="var(--warn)" stroke="#222" stroke-width="2"/><circle cx="24" cy="18" r="4" fill="#222"/><path d="M16 36c0-8 4-12 8-12s8 4 8 12z" fill="#222"/></svg>
      </div>
      <span class="volume" style="right:34px;top:22px">20L</span>
    </div>
  </section>

</main>
</body>
</html>
```